PHD-project

i need the figures to be in the same stile. info is inside the file. There are 5 figures that need redesign. this is for PhD.

Target Market(s)

it will be used in my phd

Colors

```html
<!DOCTYPE html>
<html lang="en">
<head>
<meta charset="utf-8">
<title>Reflection involves 3 Elements</title>
<link rel="stylesheet" href="https://fonts.googleapis.com/css2?family=Urbanist:ital,wght@0,400;0,500;0,600;1,400&display=swap">
<style>
  :root {
    --bg: #ffffff;
    --core: #2c759c;
    --satellite: #5e97b5;
    --overlap: #15587f;
    --on-dark: #ffffff;
    --bullet: #8ebcd8;
    --ink: #1f1f22;
    --rule: #2a2a2d;
    --quote-start: #dcdde0;
    --quote-end: rgba(255,255,255,0);
  }
  * { margin: 0; padding: 0; box-sizing: border-box; }
  html, body { width: 1200px; height: 780px; overflow: hidden; background: var(--bg); }
  body { font-family: "Urbanist", sans-serif; }
  .figure { position: relative; width: 1200px; height: 780px; }
  .diagram { position: absolute; inset: 0; }
  .circle-core { fill: var(--core); }
  .circle-satellite { fill: var(--satellite); }
  .circle-overlap { fill: var(--overlap); }
  .label-small { fill: var(--on-dark); font-size: 21px; font-weight: 500; }
  .label-large { fill: var(--on-dark); font-size: 32px; font-weight: 600; }
  .core-heading { fill: var(--on-dark); font-size: 24.5px; font-weight: 600; }
  .element-item { fill: var(--bullet); font-size: 23.5px; font-style: italic; font-weight: 400; }
  .element-dot { fill: var(--bullet); }
  .definition {
    position: absolute; left: 717px; top: 307px; width: 420px; height: 162px;
    border-left: 3px solid var(--rule);
    background: linear-gradient(90deg, var(--quote-start) 0%, var(--quote-end) 80%);
    padding: 22px 0 0 22px;
  }
  .definition p { color: var(--ink); font-size: 20px; font-weight: 500; line-height: 29.4px; white-space: nowrap; }
</style>
</head>
<body>
<main class="figure">
  <svg class="diagram" width="1200" height="780" viewBox="0 0 1200 780" aria-hidden="false">
    <defs>
      <clipPath id="core-clip"><circle cx="342" cy="389" r="224"/></clipPath>
    </defs>
    <circle class="circle-core" cx="342" cy="389" r="224"/>
    <circle class="circle-satellite" cx="566" cy="196" r="123"/>
    <circle class="circle-satellite" cx="566" cy="580" r="123"/>
    <g clip-path="url(#core-clip)">
      <circle class="circle-overlap" cx="566" cy="196" r="123"/>
      <circle class="circle-overlap" cx="566" cy="580" r="123"/>
    </g>

    <text class="label-small" x="509" y="171">Reflecting</text>
    <text class="label-large" x="508" y="208">on Action</text>
    <text class="label-small" x="509" y="590">Reflecting</text>
    <text class="label-large" x="508" y="627">in Action</text>

    <text class="core-heading" x="189" y="330">Reflection involves</text>
    <text class="core-heading" x="189" y="364">3 Elements:</text>

    <circle class="element-dot" cx="195" cy="400" r="5"/>
    <text class="element-item" x="214" y="406">Returning to Experience</text>
    <circle class="element-dot" cx="195" cy="432" r="5"/>
    <text class="element-item" x="213" y="438">Attending to Feelings</text>
    <circle class="element-dot" cx="195" cy="464" r="5"/>
    <text class="element-item" x="214" y="471">Evaluating Exerience</text>
  </svg>

  <aside class="definition">
    <p>Reflection is an active process of<br>
    witnessing one’s own experience<br>
    in order to examine it more closely,<br>
    give meaning to it, and learn from it.</p>
  </aside>
</main>
</body>
</html>
```